Redesign of business card for Cedar Ridge Mechanical

We are looking for a new design for our business cards for Cedar Ridge Mechanical. We are a plumbing & HVAC construction company, operating on the West Coast of Canada and USA. Logo attached.
Industry/Entity Type
Construction - Plumbing & HVAC
Contact Information for Business Card
Name, address, phone numbers, email, website address
Look and feel
Each slider illustrates characteristics of the customer's brand and the style your logo design should communicate.

```html
<!DOCTYPE html>
<html lang="en">
<head>
<meta charset="utf-8">
<title>Cedar Ridge Mechanical – Business Card</title>
<link href="https://fonts.googleapis.com/css2?family=Montserrat:wght@400;700&display=swap" rel="stylesheet">
<style>
  :root {
    --backdrop: #d2d2d2;
    --card-light: #f1f0ee;
    --card-dark: #0e0e0e;
    --ink: #1a1a1a;
    --ink-soft: #6e6e6e;
    --paper-white: #ffffff;
  }
  * { margin: 0; padding: 0; box-sizing: border-box; }
  html, body {
    width: 1200px; height: 1051px; overflow: hidden;
    background: var(--backdrop);
    font-family: "Montserrat", sans-serif;
  }
  .sheet {
    position: relative; width: 1200px; height: 1051px;
    display: flex; align-items: center; justify-content: center; gap: 60px;
  }
  .card {
    width: 500px; height: 286px;
    display: flex; flex-direction: column; align-items: center; justify-content: center;
  }
  .card--contact { background: var(--card-light); color: var(--ink); }
  .card--brand { background: var(--card-dark); color: var(--paper-white); }

  .contact__name { font-weight: 700; font-size: 20px; letter-spacing: 0.5px; }
  .contact__title { font-size: 13px; color: var(--ink-soft); margin-top: 2px; }
  .contact__rule { width: 40px; height: 1px; background: var(--ink); margin: 14px 0 12px; }
  .contact__list { list-style: none; font-size: 12.5px; color: var(--ink-soft); text-align: center; line-height: 1.55; }
  .contact__list li { display: flex; align-items: center; justify-content: center; gap: 6px; }
  .contact__list svg { width: 11px; height: 11px; fill: var(--ink); flex: none; }
  .contact__address { font-size: 12.5px; color: var(--ink-soft); margin-top: 2px; }

  .brand__name {
    font-weight: 700; font-size: 24px; letter-spacing: 2px; text-transform: uppercase;
    display: flex; align-items: center; gap: 12px;
  }
  .brand__mark { width: 14px; height: 14px; background: var(--paper-white); }
</style>
</head>
<body>
<main class="sheet">
  <section class="card card--contact">
    <h1 class="contact__name">MARCUS VELL</h1>
    <p class="contact__title">President</p>
    <div class="contact__rule"></div>
    <ul class="contact__list">
      <li><svg viewBox="0 0 24 24"><path d="M6.6 10.8a15.1 15.1 0 0 0 6.6 6.6l2.2-2.2a1 1 0 0 1 1-.25 11.4 11.4 0 0 0 3.6.57 1 1 0 0 1 1 1V20a1 1 0 0 1-1 1A17 17 0 0 1 3 4a1 1 0 0 1 1-1h3.5a1 1 0 0 1 1 1c0 1.25.2 2.45.57 3.6a1 1 0 0 1-.25 1z"/></svg>1-866-555-0142</li>
      <li><svg viewBox="0 0 24 24"><path d="M6.6 10.8a15.1 15.1 0 0 0 6.6 6.6l2.2-2.2a1 1 0 0 1 1-.25 11.4 11.4 0 0 0 3.6.57 1 1 0 0 1 1 1V20a1 1 0 0 1-1 1A17 17 0 0 1 3 4a1 1 0 0 1 1-1h3.5a1 1 0 0 1 1 1c0 1.25.2 2.45.57 3.6a1 1 0 0 1-.25 1z"/></svg>213-555-0198</li>
      <li><svg viewBox="0 0 24 24"><path d="M2 5h20v14H2z M2 5l10 8 10-8" /></svg>info@cedarridgemech.com</li>
      <li><svg viewBox="0 0 24 24"><circle cx="12" cy="12" r="10"/></svg>www.cedarridgemech.com</li>
    </ul>
    <p class="contact__address">4120 Harbor Lane, Suite 200, Irvine, CA 92614</p>
  </section>

  <section class="card card--brand">
    <div class="brand__name"><span class="brand__mark"></span>Cedar Ridge Mechanical</div>
  </section>
</main>
</body>
</html>
```